Oil and Gas Exploration and Production company needs a business card design

We need a business card design using our logo and colors in the logo. We want a mainstream design.

```html
<!DOCTYPE html>
<html lang="en">
<head>
<meta charset="UTF-8">
<title>Vesta Oil &amp; Gas — Business Card</title>
<link rel="stylesheet" href="https://fonts.googleapis.com/css2?family=Work+Sans:wght@400;500;600;700&display=swap">
<style>
  :root {
    --backdrop: #2b2b2c;
    --card-dark: #050607;
    --card-mid: #16191b;
    --gold: #d9a530;
    --white: #ffffff;
    --soft-white: #e9e9e9;
  }
  * { box-sizing: border-box; margin: 0; padding: 0; }
  html, body {
    width: 1200px;
    height: 930px;
    overflow: hidden;
    background: var(--backdrop);
    font-family: "Work Sans", sans-serif;
  }
  .canvas {
    position: relative;
    width: 1200px;
    height: 930px;
  }
  .card {
    position: absolute;
    width: 660px;
    height: 377px;
    border-radius: 14px;
    background: linear-gradient(115deg, var(--card-dark) 0%, var(--card-mid) 48%, var(--card-dark) 100%);
    box-shadow: 0 18px 40px rgba(0, 0, 0, 0.55);
    overflow: hidden;
  }
  .card--front { left: 110px; top: 70px; }
  .card--back  { left: 430px; top: 480px; }

  .brand {
    position: absolute;
    display: flex;
    align-items: center;
    gap: 14px;
    color: var(--white);
    font-weight: 700;
    white-space: nowrap;
  }
  .brand__dot {
    width: 40px;
    height: 40px;
    border-radius: 50%;
    background: var(--gold);
    flex: none;
  }
  .card--front .brand {
    left: 50%;
    top: 50%;
    transform: translate(-50%, -50%);
    font-size: 44px;
  }
  .card--back .brand {
    left: 44px;
    top: 236px;
    font-size: 32px;
  }
  .card--back .brand__dot { width: 32px; height: 32px; }

  .divider {
    position: absolute;
    left: 370px;
    top: 64px;
    width: 2px;
    height: 250px;
    background: var(--gold);
  }
  .contact {
    position: absolute;
    left: 398px;
    top: 70px;
    color: var(--soft-white);
    font-size: 14px;
    line-height: 1.45;
  }
  .contact__name {
    color: var(--gold);
    font-size: 26px;
    font-weight: 600;
    line-height: 1.1;
  }
  .contact__role { margin-bottom: 16px; }
  .contact__address { margin-bottom: 14px; }
  .contact__line {
    display: flex;
    align-items: center;
    gap: 8px;
  }
  .contact__line svg { width: 12px; height: 12px; flex: none; }
  .contact__accent { color: var(--gold); }
</style>
</head>
<body>
<main class="canvas">
  <section class="card card--front" aria-label="Card front">
    <div class="brand"><span class="brand__dot"></span>Vesta Oil &amp; Gas</div>
  </section>

  <section class="card card--back" aria-label="Card back">
    <div class="brand"><span class="brand__dot"></span>Vesta Oil &amp; Gas</div>
    <div class="divider"></div>
    <div class="contact">
      <p class="contact__name">Dale Hartwell</p>
      <p class="contact__role">CFO</p>
      <p class="contact__address">4821 Ridgeline Blvd,<br>Fort Worth, Texas us</p>
      <p class="contact__line">
        <svg viewBox="0 0 12 12" aria-hidden="true"><path d="M2.5 1h2l1 2.5-1.3 1a6 6 0 0 0 3.3 3.3l1-1.3L11 7.5v2A1.5 1.5 0 0 1 9.5 11 8.5 8.5 0 0 1 1 2.5 1.5 1.5 0 0 1 2.5 1z" fill="var(--gold)"/></svg>
        (555) 014-2277
      </p>
      <p class="contact__line">
        <svg viewBox="0 0 12 12" aria-hidden="true"><rect x="1" y="2.5" width="10" height="7" rx="1" fill="none" stroke="var(--gold)" stroke-width="1.2"/><path d="M1.5 3l4.5 3.5L10.5 3" fill="none" stroke="var(--gold)" stroke-width="1.2"/></svg>
        info@vestaoil&amp;gas.com
      </p>
      <p class="contact__line">
        <svg viewBox="0 0 12 12" aria-hidden="true"><circle cx="6" cy="6" r="5" fill="none" stroke="var(--gold)" stroke-width="1.1"/><ellipse cx="6" cy="6" rx="2.2" ry="5" fill="none" stroke="var(--gold)" stroke-width="1"/><path d="M1 6h10" stroke="var(--gold)" stroke-width="1"/></svg>
        <span>www.<span class="contact__accent">vestaoil&amp;gas</span>.com</span>
      </p>
    </div>
  </section>
</main>
</body>
</html>
```